Card design for orthopaedic surgeons working as The Brightwater Joint Centre

Business cards, letterhead

Colors

Designer to choose colors to be used in the design.

Requirements
Must have
• Late addition.
• Cards letterhead must have logos of
• Crestmoor Lindell College of Surgeons
• Varenwood Bone Health Association
Nice to have
• Back of card to have space for appointment time to be added by hand and some blank space for writing incidental other notes.

```html
<!DOCTYPE html>
<html lang="en">
<head>
<meta charset="utf-8">
<title>The Brightwater Joint Centre – Business Card</title>
<link rel="stylesheet" href="https://fonts.googleapis.com/css2?family=Open+Sans:wght@400;600&family=Arimo:wght@400;700&display=swap">
<style>
  :root {
    --page-bg: #d9dadc;
    --card-white: #ffffff;
    --sky-blue: #35b1fb;
    --navy: #06304f;
    --ink: #1d1d1d;
    --logo-blue: #2a9ad8;
    --rule-grey: #c9c9c9;
  }
  * { box-sizing: border-box; margin: 0; padding: 0; }
  html, body {
    width: 1200px; height: 1200px; overflow: hidden;
    background: var(--page-bg);
  }
  .sheet {
    position: relative; width: 1200px; height: 1200px;
  }
  .card {
    position: absolute; left: 150px;
    width: 900px; height: 514px;
    background: var(--card-white);
    border-radius: 40px;
    overflow: hidden;
    box-shadow: 0 2px 6px rgba(0,0,0,0.12);
    font-family: "Open Sans", sans-serif;
    color: var(--ink);
  }
  .card-back { top: 50px; }
  .card-front { top: 630px; }

  /* Back */
  .back-brand {
    position: absolute; left: 0; right: 0; top: 190px;
    display: flex; flex-direction: column; align-items: center; gap: 26px;
  }
  .brand-name {
    display: flex; align-items: center; gap: 14px;
    font-family: "Open Sans", sans-serif; font-weight: 400;
    color: var(--logo-blue);
    white-space: nowrap;
  }
  .brand-dot {
    width: 22px; height: 22px; border-radius: 50%;
    background: var(--logo-blue);
  }
  .card-back .brand-name { font-size: 44px; }
  .back-web {
    font-size: 25px; letter-spacing: 0.32em; color: var(--ink);
  }

  /* Front */
  .front-art { position: absolute; inset: 0; }
  .holder {
    position: absolute; right: 70px; top: 130px; text-align: right;
    font-family: "Arimo", sans-serif; color: var(--navy);
  }
  .holder-name { font-weight: 700; font-size: 40px; line-height: 1.1; }
  .holder-title { font-weight: 400; font-size: 30px; color: #0d1c2a; margin-top: 4px; }
  .card-front .brand-name {
    position: absolute; left: 60px; top: 212px; font-size: 32px; gap: 12px;
  }
  .card-front .brand-dot { width: 17px; height: 17px; }
  .contacts {
    position: absolute; left: 60px; top: 320px;
    list-style: none; font-size: 21px; line-height: 38px;
  }
  .contacts li { display: flex; align-items: center; gap: 14px; }
  .contacts svg { width: 20px; height: 20px; flex: none; }
  .divider {
    position: absolute; left: 430px; top: 360px;
    width: 2px; height: 70px; background: var(--rule-grey);
  }
  .address {
    position: absolute; left: 460px; top: 358px;
    font-size: 21px; line-height: 34px; font-style: normal;
  }
</style>
</head>
<body>
<main class="sheet">

  <section class="card card-back" aria-label="Card back">
    <div class="back-brand">
      <div class="brand-name"><span class="brand-dot"></span>The Brightwater Joint Centre</div>
      <div class="back-web">www.brightwaterjoint.example</div>
    </div>
  </section>

  <section class="card card-front" aria-label="Card front">
    <svg class="front-art" viewBox="0 0 900 514" preserveAspectRatio="none" aria-hidden="true">
      <path d="M0,0 H900 V372 C720,230 440,30 0,30 Z" fill="var(--sky-blue)"/>
      <path d="M0,48 C420,40 700,225 900,395 L900,418 C690,245 410,58 0,58 Z" fill="var(--navy)"/>
    </svg>

    <div class="holder">
      <div class="holder-name">Maren Holt</div>
      <div class="holder-title">Title</div>
    </div>

    <div class="brand-name"><span class="brand-dot"></span>The Brightwater Joint Centre</div>

    <ul class="contacts">
      <li>
        <svg viewBox="0 0 20 20" aria-hidden="true"><circle cx="10" cy="10" r="10" fill="var(--sky-blue)"/><path d="M7 5 L9 7.5 L8 9 C8.8 10.8 9.6 11.6 11 12.2 L12.5 11 L15 13 L13.5 15 C9 14.5 5.5 11 5 6.5 Z" fill="#fff"/></svg>
        012-555-0148
      </li>
      <li>
        <svg viewBox="0 0 20 20" aria-hidden="true"><circle cx="10" cy="10" r="10" fill="var(--sky-blue)"/><rect x="5" y="6.5" width="10" height="7" fill="#fff"/><path d="M5 6.5 L10 10.5 L15 6.5" fill="none" stroke="var(--sky-blue)" stroke-width="1.2"/></svg>
        info@brightwaterjoint.example
      </li>
      <li>
        <svg viewBox="0 0 20 20" aria-hidden="true"><circle cx="10" cy="10" r="10" fill="var(--sky-blue)"/><circle cx="10" cy="10" r="5.5" fill="none" stroke="#fff" stroke-width="1.2"/><path d="M4.5 10 H15.5 M10 4.5 C7.5 7 7.5 13 10 15.5 M10 4.5 C12.5 7 12.5 13 10 15.5" fill="none" stroke="#fff" stroke-width="1"/></svg>
        www.brightwaterjoint.example
      </li>
    </ul>

    <div class="divider"></div>
    <address class="address">
      Street Name, City Name<br>
      Zipcode - 012345
    </address>
  </section>

</main>
</body>
</html>
```